Veltrano.co - Polar Expeditions Specialists

We need a modern, visually striking business card for Veltrano.co, a company specialized in selling expedition cruises to the most remote regions on Earth, with a focus on the Arctic and Antarctica. The design should instantly communicate that the cardholder is an expert in polar travel. Use clean, premium aesthetics with cool tones like icy blue and white, possibly incorporating polar imagery (ice, glaciers, penguins, etc.)

Attached the logo

Contact Information for Business Card

Feels high-end and trustworthy.. Visually memorable — encourages people to keep it

Colors
0054AA
0677BA
7BADD7
CADEEF
E8F1F8

Requirements
Must have
• ice, glaciers, penguins, montains
Nice to have
• modern, transparente,

```html
<!DOCTYPE html>
<html lang="en">
<head>
<meta charset="utf-8">
<title>Veltrano.co Business Card</title>
<link href="https://fonts.googleapis.com/css2?family=Poppins:wght@400;600;700&family=Open+Sans:wght@400;600&display=swap" rel="stylesheet">
<style>
  :root {
    --bg: #2b2b2d;
    --white: #ffffff;
    --brand-deep: #0054AA;
    --brand: #0677BA;
    --brand-mid: #3a86cc;
    --brand-soft: #7BADD7;
    --ice: #CADEEF;
    --frost: #E8F1F8;
  }
  * { box-sizing: border-box; margin: 0; padding: 0; }
  html, body { width: 1200px; height: 875px; overflow: hidden; }
  body {
    background: var(--bg);
    position: relative;
    font-family: 'Open Sans', sans-serif;
  }
  .card {
    position: absolute;
    width: 520px;
    height: 300px;
    border-radius: 18px;
    overflow: hidden;
    box-shadow: 0 18px 40px rgba(0,0,0,.45);
  }
  /* Front */
  .card-front {
    left: 70px; top: 140px;
    background: var(--white);
    display: flex; align-items: center; justify-content: center;
  }
  .brand { display: flex; flex-direction: column; align-items: flex-start; }
  .brand-row { display: flex; align-items: center; gap: 14px; }
  .brand-dot { width: 18px; height: 18px; border-radius: 50%; background: var(--brand); }
  .brand-name {
    font-family: 'Poppins', sans-serif; font-weight: 700;
    font-size: 52px; line-height: 1; color: var(--brand);
    letter-spacing: .5px;
  }
  .brand-tagline {
    font-family: 'Poppins', sans-serif; font-weight: 600;
    font-size: 14px; color: var(--brand); margin: 6px 0 0 34px;
  }
  /* Back */
  .card-back {
    left: 610px; top: 430px;
    background: linear-gradient(160deg, var(--brand-mid) 0%, var(--brand) 55%, var(--brand-deep) 100%);
    color: var(--white);
  }
  .scene-glacier {
    position: absolute; left: 0; bottom: 0; width: 100%; height: 55%;
    background: linear-gradient(180deg, rgba(202,222,239,0) 0%, rgba(123,173,215,.35) 60%, rgba(0,84,170,.35) 100%);
  }
  .scene-animals {
    position: absolute; right: 0; top: 0; width: 210px; height: 100%;
    background: linear-gradient(170deg, var(--white) 0%, var(--frost) 55%, var(--ice) 100%);
    border-top-left-radius: 90px 120px;
  }
  .back-content { position: absolute; left: 32px; top: 30px; width: 270px; }
  .back-content .brand-name { color: var(--white); font-size: 40px; }
  .back-content .brand-tagline { color: var(--white); font-size: 12px; margin: 4px 0 0 0; }
  .person-name {
    font-family: 'Poppins', sans-serif; font-weight: 700;
    font-size: 19px; letter-spacing: .5px; margin-top: 16px; line-height: 1.1;
  }
  .person-title { font-size: 14px; margin-bottom: 12px; }
  .contact-list { list-style: none; font-size: 11.5px; line-height: 1.45; }
  .contact-list li { display: flex; align-items: flex-start; gap: 8px; }
  .contact-list svg { width: 11px; height: 11px; margin-top: 3px; flex: none; fill: var(--white); }
</style>
</head>
<body>
  <section class="card card-front">
    <div class="brand">
      <div class="brand-row">
        <span class="brand-dot"></span>
        <span class="brand-name">Veltrano.co</span>
      </div>
      <span class="brand-tagline">Polar Expeditions Specialists</span>
    </div>
  </section>

  <section class="card card-back">
    <div class="scene-glacier" role="img" aria-label="Icy glacier and mountain landscape in blue tones"></div>
    <div class="scene-animals" role="img" aria-label="White silhouette of a polar bear with penguins"></div>
    <div class="back-content">
      <div class="brand-name">Veltrano.co</div>
      <div class="brand-tagline">Polar Expeditions Specialists</div>
      <div class="person-name">DANIEL ROWE</div>
      <div class="person-title">Founder &amp; CEO</div>
      <ul class="contact-list">
        <li><svg viewBox="0 0 12 12"><path d="M6 0a4 4 0 0 0-4 4c0 3 4 8 4 8s4-5 4-8a4 4 0 0 0-4-4zm0 5.5A1.5 1.5 0 1 1 6 2.5a1.5 1.5 0 0 1 0 3z"/></svg><span>218 Harbour Quay Road<br>Northport, Maine, USA, 04110</span></li>
        <li><svg viewBox="0 0 12 12"><path d="M2.5 0.5l2 2.5-1 1.5c.8 1.6 2 2.8 3.6 3.6l1.5-1 2.4 2-1.2 2.3C5 11 1 7 .4 1.7z"/></svg><span>(555) 210-4471</span></li>
        <li><svg viewBox="0 0 12 12"><path d="M3 0h6a1 1 0 0 1 1 1v10a1 1 0 0 1-1 1H3a1 1 0 0 1-1-1V1a1 1 0 0 1 1-1zm0 1.5v8h6v-8zM6 10.2a.6.6 0 1 0 0 1.2.6.6 0 0 0 0-1.2z"/></svg><span>(555) 210-4471</span></li>
        <li><svg viewBox="0 0 12 12"><path d="M0 2h12v8H0zm1 1v.3l5 3.5 5-3.5V3zm0 1.5V9h10V4.5L6 8z"/></svg><span>info@veltranotravel.com</span></li>
        <li><svg viewBox="0 0 12 12"><path d="M6 0a6 6 0 1 0 0 12A6 6 0 0 0 6 0zm0 1c.8 0 1.6 1.9 1.8 4.5H4.2C4.4 2.9 5.2 1 6 1zM1 6.5h2.2c.1 1.7.5 3.2 1 4.1A5 5 0 0 1 1 6.5zm0-1a5 5 0 0 1 3.2-4.1c-.5.9-.9 2.4-1 4.1zm5 5.5c-.8 0-1.6-1.9-1.8-4.5h3.6C7.6 9.1 6.8 11 6 11zm1.8-.4c.5-.9.9-2.4 1-4.1H11a5 5 0 0 1-3.2 4.1zM8.8 5.5c-.1-1.7-.5-3.2-1-4.1A5 5 0 0 1 11 5.5z"/></svg><span>veltranotravel.com</span></li>
      </ul>
    </div>
  </section>
</body>
</html>
```